Website Design for StratoNest as a Service

We are building a service to allow customers to own their own private clouds easily and cheaply. Owning your own private cloud saves costs, and offers more flexibility than a public cloud provider but has historically been a complex and expensive option.

We plan to offer a service where we build and maintain your own private cloud on your own hardware for a cheap monthly costs. Similar to this service - https://nimbrovex.com/solutions/private-cloud

We already have a logo and branding in place - we'd like a website design to be tailored from this branding, see attached logo design.

Feel free to add important elements on the home page such as testimonials, client/partner logos, contact form, social media, etc using placeholder contents in addition to the document we attached.

We also plan to add sub-pages in the future so please make sure that your website design has a full navigation menu.

An example of the site we like: https://www.quorvant.com/ we'd be happy for you to take inspiration from this website.

Target Market(s)

B2B focused, we are targeting start-up/small/medium sized companies who needs help with their cloud and IT infrastructure.

Industry/Entity Type

IT

Number of Pages Required

1 page

Font styles to use
Other font styles liked:
• Please refer to the attachment - font must have Mayeka Demi Bold & Retroica

Requirements
Must have
• Please add placeholder menu since we're planning to have subpages later on.

```html
<!DOCTYPE html>
<html lang="en">
<head>
<meta charset="utf-8">
<title>StratoNest as a Service</title>
<link rel="stylesheet" href="https://fonts.googleapis.com/css2?family=Comfortaa:wght@500;700&family=Montserrat:wght@400;500;600;700&display=swap">
<style>
:root{
  --navy:#0a1f5c;
  --navy-deep:#061442;
  --blue:#1f78c1;
  --blue-bright:#2a8fe0;
  --sky:#4fb3ff;
  --ink:#1c1c1c;
  --grey:#555a63;
  --soft:#f4f8fc;
  --badge:#f2f2f2;
  --white:#ffffff;
}
*{box-sizing:border-box;margin:0;padding:0}
html,body{width:1200px;height:4552px;overflow:hidden}
body{font-family:"Montserrat",sans-serif;color:var(--ink);background:var(--white);position:relative}
.display{font-family:"Comfortaa",sans-serif;font-weight:700}
section,header,footer{position:absolute;left:0;width:1200px}
.abs{position:absolute}
.btn{position:absolute;display:flex;align-items:center;justify-content:center;border-radius:30px;font-size:11px;font-weight:700;letter-spacing:.5px;text-transform:uppercase;z-index:2}
.btn--white{background:var(--white);color:var(--navy)}
.btn--blue{background:var(--blue-bright);color:var(--white)}
.art{position:absolute;border-radius:14px}

/* hero */
.hero{top:0;height:678px;background:radial-gradient(ellipse at 50% 90%,#1a5fc4 0%,#0c2a78 40%,var(--navy-deep) 80%);color:var(--white);overflow:hidden}
.brand{position:absolute;display:flex;align-items:center;gap:10px}
.brand__dot{width:30px;height:30px;border-radius:50%;background:var(--white)}
.brand__name{font-family:"Montserrat",sans-serif;font-weight:600;font-size:30px;color:var(--white);line-height:1}
.brand__sub{font-size:11px;font-weight:600;color:var(--white);position:absolute;right:0;top:33px}
.nav{position:absolute;left:561px;top:71px;display:flex;gap:36px;font-size:13px;font-weight:500}
.hero__title{position:absolute;top:168px;width:100%;text-align:center;font-size:31px;line-height:37px}
.hero__lead{position:absolute;top:258px;width:100%;text-align:center;font-size:15px;line-height:23px}
.hero__ask{position:absolute;top:352px;width:100%;text-align:center;font-size:15px;font-weight:700}
.hero__art{left:380px;top:420px;width:440px;height:258px;background:radial-gradient(ellipse at 50% 60%,#3f9bff 0%,#1554b8 50%,rgba(10,31,92,0) 80%);border-radius:50% 50% 0 0}

/* benefits */
.benefits{top:678px;height:625px}
.section-title{position:absolute;width:100%;text-align:center;font-size:27px;color:var(--ink)}
.benefit{position:absolute;width:260px;text-align:center}
.benefit__icon{margin:0 auto 30px;width:120px;height:86px;border-radius:44px;background:var(--white);box-shadow:0 8px 22px rgba(20,60,120,.12);display:flex;align-items:center;justify-content:center}
.benefit__icon span{width:34px;height:34px;border-radius:8px;border:2px solid var(--blue-bright)}
.benefit h3{font-size:14px;font-weight:700;line-height:18px;margin-bottom:14px}
.benefit p{font-size:11px;color:var(--grey);line-height:14px}

/* transform */
.transform{top:1303px;height:583px;background:var(--blue);color:var(--white);overflow:hidden}
.transform h2{position:absolute;left:159px;top:100px;font-size:27px;line-height:33px;width:440px;z-index:2}
.transform p{position:absolute;left:159px;width:445px;font-size:12px;line-height:22px;z-index:2}
.transform__art{left:620px;top:40px;width:580px;height:543px;border-radius:0;background:linear-gradient(160deg,#2b9bf0 0%,#1463b8 55%,#0e3d8c 100%);z-index:1}

/* public cloud */
.public{top:1886px;height:619px}
.public__art{left:38px;top:110px;width:562px;height:430px;background:radial-gradient(ellipse at 50% 55%,#d6ecff 0%,#eef7ff 55%,#ffffff 80%)}
.public h2{position:absolute;left:618px;top:94px;font-size:27px;line-height:33px}
.point{position:absolute;left:618px;width:420px}
.point h4{font-size:12.5px;font-weight:700;margin-bottom:7px}
.point p{font-size:12px;line-height:22px;color:var(--grey)}

/* testimonials */
.reviews{top:2505px;height:451px;background:var(--soft)}
.review{position:absolute;top:160px;width:270px}
.review__mark{font-family:"Comfortaa",sans-serif;font-weight:700;font-size:84px;color:var(--blue-bright);line-height:64px;height:40px;overflow:visible}
.review p{margin-top:10px;font-size:12px;line-height:20px;color:#7a7f88}
.review p a{color:#7a7f88;margin-left:8px;text-decoration:underline}
.review__who{display:flex;align-items:center;gap:12px;margin-top:14px}
.avatar{width:48px;height:48px;border-radius:50%;background:#3a3a3a;color:var(--white);display:flex;align-items:center;justify-content:center;font-size:22px}
.review__name{font-size:15px;color:var(--blue-bright);font-weight:500}
.stars{color:#f5c000;font-size:16px;letter-spacing:2px}
.dots{position:absolute;top:386px;left:0;width:100%;display:flex;justify-content:center;gap:14px}
.dots span{width:6px;height:6px;border-radius:50%;background:var(--ink)}

/* difference */
.difference{top:2956px;height:550px}
.difference h2{position:absolute;left:142px;top:80px;font-size:27px}
.difference__list{position:absolute;left:142px;top:143px;width:480px;font-size:12px;line-height:16px;color:#333}
.difference__list p{margin-bottom:17px}
.difference__art{left:628px;top:54px;width:522px;height:430px;background:linear-gradient(150deg,#e6f3ff 0%,#bfe0ff 50%,#eaf5ff 100%)}

/* partners */
.partners{top:3506px;height:469px}
.badge{position:absolute;width:143px;height:142px;background:var(--badge);display:flex;align-items:center;justify-content:center}
.badge i{display:block;width:78px;height:78px;border-radius:50%;background:linear-gradient(160deg,#2a8fe0,#1a3f8f)}
.badge i.hex{border-radius:14px;background:linear-gradient(160deg,#5b2aa0,#2a1a6b)}

/* footer */
.footer{top:3975px;height:577px;background:radial-gradient(ellipse at 50% 40%,#123a8c 0%,var(--navy) 55%,var(--navy-deep) 100%);color:var(--white)}
.footer h5{position:absolute;left:159px;top:186px;font-size:11px;font-weight:700;text-decoration:underline}
.contact{position:absolute;left:159px;display:flex;gap:18px;font-size:12px;line-height:22px;align-items:flex-start}
.contact svg{flex:none;margin-top:3px}
.social{position:absolute;left:159px;top:398px;display:flex;gap:32px}
.social span{width:26px;height:26px;border-radius:50%;border:2px solid var(--white)}
.copy{position:absolute;left:159px;top:480px;font-size:11px}
.field{position:absolute;background:var(--white);border-radius:26px;color:#8a8f98;font-size:11px;padding:16px 18px}
.submit{color:var(--navy)}
</style>
</head>
<body>

<header class="hero">
  <div class="brand" style="left:142px;top:48px">
    <span class="brand__dot"></span>
    <span class="brand__name">StratoNest</span>
    <span class="brand__sub">AS A SERVICE</span>
  </div>
  <nav class="nav">
    <span>Home</span><span>About</span><span>Services</span><span>Why Us</span><span>Partners</span><span>Contact</span>
  </nav>
  <h1 class="hero__title display">A groundbreaking way for your small business<br>to benefit from the power of the cloud</h1>
  <p class="hero__lead">StratoNest as a Service is here to help small businesses utilise the power<br>of the cloud without complicated set-ups or scary price tags.</p>
  <p class="hero__ask">Ready to modernise your infrastructure with a fully managed private cloud solution from SNaaS?</p>
  <div class="btn btn--white" style="left:517px;top:400px;width:168px;height:53px">Contact Us</div>
  <div class="art hero__art" role="img" aria-label="Glowing digital globe with a cloud symbol rising from a circuit board"></div>
</header>

<section class="benefits">
  <h2 class="section-title display" style="top:72px">How SNAAS benefits your business</h2>
  <div class="benefit" style="left:181px;top:152px"><div class="benefit__icon" role="img" aria-label="Flexibility icon"><span></span></div><h3>Totally flexible</h3><p>get the cloud you want and the<br>latest innovations you need</p></div>
  <div class="benefit" style="left:469px;top:152px"><div class="benefit__icon" role="img" aria-label="Speed icon"><span></span></div><h3>Faster</h3><p>our private cloud solutions<br>outpace public clouds</p></div>
  <div class="benefit" style="left:757px;top:152px"><div class="benefit__icon" role="img" aria-label="Value icon"><span></span></div><h3>Greater value for money</h3><p>totally transparent pricing for no<br>nasty month-end surprises</p></div>
  <div class="benefit" style="left:181px;top:366px"><div class="benefit__icon" role="img" aria-label="Fees icon"><span></span></div><h3>No consultancy fees</h3><p style="margin-top:24px">we'll work with you and charge<br>set fees for everything</p></div>
  <div class="benefit" style="left:469px;top:366px"><div class="benefit__icon" role="img" aria-label="Monitoring icon"><span></span></div><h3>Management, monitoring<br>and maintenance</h3><p>they're all included in your<br>monthly price</p></div>
  <div class="benefit" style="left:757px;top:366px"><div class="benefit__icon" role="img" aria-label="Tested solutions icon"><span></span></div><h3>Tried and tested cloud<br>solutions</h3><p>we'll deploy the right OpenStrata<br>suite of products for your business</p></div>
</section>

<section class="transform">
  <h2 class="display">SNAAS can drive your digital transformation today</h2>
  <p style="top:198px">Organisations of all shapes and sizes are reaping the time and money saving benefits that the cloud brings.</p>
  <p style="top:265px">But for small businesses seeking to transition, managing the time and financial costs of transitioning, and knowing whether to opt for a public or private cloud can cause you to hit the pause button.</p>
  <p style="top:354px">SNAAS is here to help you switch on your cloud transformation in a way that works best for you.  We deliver and support fully managed private cloud solutions that are:</p>
  <div class="btn btn--white" style="left:159px;top:461px;width:159px;height:46px;color:var(--blue)">Get Started</div>
  <div class="art transform__art" role="img" aria-label="Isometric city of data blocks with a laptop and labels Fast, Scalable, Easy and Powerful"></div>
</section>

<section class="public">
  <div class="art public__art" role="img" aria-label="Isometric laptop, phone and server stack with people working on cloud data"></div>
  <h2 class="display">If you're using a public<br>cloud now</h2>
  <div class="point" style="top:190px"><h4>You could be paying too much...</h4><p>Public cloud pricing structures have a habit of sneakily scaling up very quickly. With SNAAS, you'll always know what you're paying for your private cloud services.</p></div>
  <div class="point" style="top:302px"><h4>You're likely not getting the benefits of full functionality...</h4><p>Public cloud providers cannot adopt new innovations and functions as quickly and easily as the private cloud solutions you'll get from SNAAS.</p></div>
  <div class="point" style="top:414px"><h4>You'll be tied to the services your provider can provide...</h4><p>Public cloud providers will have a limited suite of products and services to offer you. A SNAAS private cloud has no such limitations</p></div>
  <div class="btn btn--blue" style="left:618px;top:515px;width:148px;height:47px">Let's Talk</div>
</section>

<section class="reviews">
  <h2 class="section-title display" style="top:88px">What Our Customer Says</h2>
  <div class="review" style="left:162px"><div class="review__mark">&ldquo;</div><p>Lorem ipsum dolor sit amet, consectetur adipisicing elit, sed do eiusmod tempor incididunt ut labore et dolore magna aliqua. Ut enim ad minim veniam. <a>read more</a></p><div class="review__who"><div class="avatar">J</div><div><div class="review__name">Jhoan Deo</div><div class="stars">★★★★★</div></div></div></div>
  <div class="review" style="left:468px"><div class="review__mark">&ldquo;</div><p>Lorem ipsum dolor sit amet, consectetur adipisicing elit, sed do eiusmod tempor incididunt ut labore et dolore magna aliqua. Ut enim ad minim veniam. <a>read more</a></p><div class="review__who"><div class="avatar">J</div><div><div class="review__name">Jhoan Deo</div><div class="stars">★★★★★</div></div></div></div>
  <div class="review" style="left:773px"><div class="review__mark">&ldquo;</div><p>Lorem ipsum dolor sit amet, consectetur adipisicing elit, sed do eiusmod tempor incididunt ut labore et dolore magna aliqua. Ut enim ad minim veniam. <a>read more</a></p><div class="review__who"><div class="avatar">J</div><div><div class="review__name">Jhoan Deo</div><div class="stars">★★★★★</div></div></div></div>
  <div class="dots"><span></span><span></span><span></span></div>
</section>

<section class="difference">
  <h2 class="display">The SNAAS Difference</h2>
  <div class="difference__list">
    <p>We'll quickly get to grips with what your organisation needs, and deliver it via our private cloud solutions.</p>
    <p>Enjoy the ease of the public cloud, combined with the features, innovations and flexibility of the private cloud.</p>
    <p>You can focus on your core business while we support you with a dedicated cloud infrastructure.</p>
    <p>We'll create and deliver the launchpad that will take your business forward.</p>
    <p>Get the benefits of your own cloud infrastructure and reduce your operational costs</p>
    <p>Fast and easy computing, storage and network resources</p>
    <p>Managed operations from private OpenStrata clouds and Helmgrid</p>
    <p>We'll support your growth and scale your cloud as you need it.</p>
  </div>
  <div class="btn btn--blue" style="left:142px;top:481px;width:148px;height:45px">Let's Talk</div>
  <div class="art difference__art" role="img" aria-label="Isometric laptop on a grid with a cloud upload symbol and floating clouds"></div>
</section>

<section class="partners">
  <h2 class="section-title display" style="top:62px">Our Parents</h2>
  <div class="badge" style="left:205px;top:114px" role="img" aria-label="Partner certification badge"><i class="hex"></i></div>
  <div class="badge" style="left:367px;top:114px" role="img" aria-label="Partner certification badge"><i style="border-radius:8px"></i></div>
  <div class="badge" style="left:530px;top:114px" role="img" aria-label="Partner certification badge"><i></i></div>
  <div class="badge" style="left:691px;top:114px" role="img" aria-label="Partner certification badge"><i style="border-radius:6px;background:#1a3f8f"></i></div>
  <div class="badge" style="left:853px;top:114px" role="img" aria-label="Partner certification badge"><i class="hex" style="background:linear-gradient(160deg,#b01a5a,#5a1a6b)"></i></div>
  <div class="badge" style="left:367px;top:276px" role="img" aria-label="Partner accreditation badge"><i style="border-radius:10px;background:linear-gradient(180deg,#ffffff,#bfe0ff)"></i></div>
  <div class="badge" style="left:530px;top:276px" role="img" aria-label="Partner certification badge"><i style="background:#ffffff;border:3px dashed #2a8fe0"></i></div>
  <div class="badge" style="left:691px;top:276px" role="img" aria-label="Partner certification badge"><i class="hex" style="background:linear-gradient(160deg,#2a1a8f,#1a1a4f)"></i></div>
</section>

<footer class="footer">
  <div class="brand" style="left:430px;top:62px">
    <span class="brand__dot"></span>
    <span class="brand__name" style="font-size:34px">StratoNest</span>
    <span class="brand__sub" style="top:38px">AS A SERVICE</span>
  </div>
  <h5>CONTACT US</h5>
  <div class="contact" style="top:226px">
    <svg width="12" height="16" viewBox="0 0 12 16"><path d="M6 0a6 6 0 0 0-6 6c0 4.5 6 10 6 10s6-5.5 6-10a6 6 0 0 0-6-6zm0 8.5A2.5 2.5 0 1 1 6 3.5a2.5 2.5 0 0 1 0 5z" fill="#fff"/></svg>
    <span>Add your address line<br>here abc 123456</span>
  </div>
  <div class="contact" style="top:292px">
    <svg width="15" height="15" viewBox="0 0 15 15"><path d="M3 0l3 3-1.6 2.2a9 9 0 0 0 5.4 5.4L12 9l3 3-2 3C6 15 0 9 0 2z" fill="#fff"/></svg>
    <span>+01 23 456 7890</span>
  </div>
  <div class="contact" style="top:336px">
    <svg width="15" height="11" viewBox="0 0 15 11"><rect width="15" height="11" rx="1" fill="#fff"/><path d="M0 1l7.5 5L15 1" stroke="#0a1f5c" stroke-width="1.4" fill="none"/></svg>
    <span>info@stratonestasaservice.com</span>
  </div>
  <div class="social" role="img" aria-label="Social media links"><span></span><span></span><span></span><span></span></div>
  <p class="copy">© 2022 StratoNest As a Service. All Rights Reserved</p>
  <div class="field" style="left:535px;top:168px;width:500px;height:49px">Name</div>
  <div class="field" style="left:535px;top:240px;width:235px;height:49px">Email</div>
  <div class="field" style="left:799px;top:240px;width:236px;height:49px">Number</div>
  <div class="field" style="left:535px;top:311px;width:500px;height:124px">Description</div>
  <div class="btn btn--white submit" style="left:900px;top:459px;width:135px;height:48px">Submit</div>
</footer>

</body>
</html>
```